Web design for a honey company

We are a honey retailing company currently looking for creative design for 3 pages of our existing e-commerce website which can be found here www.alpha.tolvenmarsk.co.nz. The designs need to be responsive i.e. presented in both desktop and mobile versions. We want to use the existing page color pallet, however any fonts can be used. Please use the texts and graphic content in the attachment files provided. For more detailed instructions please. The page does not require coding, the output files should be provided as layered and editable PSD.<br/><br/>Task 2: design 2 home page banners. Images, texts and the concept provided in the "layout structure" file. <br/><br/>The web designs should be presented in both desktop and mobile versions. We are looking for professional designer submissions only!

Target Market(s)

Hi-end consumers
Health conscious consumers

Number of Pages Required

3 page

Requirements
Must have
• 50% of images supplied along + any suggested stock images.
• Supplied texts integrated in the designs.
• Please only use the product images we have provided!
Should not have
• Clipart vector bees, vector honey slots or combs.
• No images of honey in glass jars!
• Do not use images of the traditional honey wooden spoons!
• Do not use images of any other but Manuka flower!

```html
<!DOCTYPE html>
<html lang="en">
<head>
<meta charset="utf-8">
<title>Tolvenmarsk – Honey from New Zealand</title>
<link href="https://fonts.googleapis.com/css2?family=Anton&family=Libre+Baskerville&family=Poppins:wght@400;500&display=swap" rel="stylesheet">
<style>
:root{
  --gold:#e2b64a;
  --gold-light:#f2d77b;
  --gold-pale:#fdf7e6;
  --ink:#151515;
  --text:#5a5a5a;
  --white:#fff;
  --grad:linear-gradient(90deg,#f3d97e,#dfb24a);
}
*{margin:0;padding:0;box-sizing:border-box}
html,body{width:1200px;height:4120px;overflow:hidden;background:var(--white)}
body{font-family:"Poppins",sans-serif;color:var(--text);position:relative}
.abs{position:absolute}
.btn{position:absolute;display:flex;align-items:center;justify-content:center;gap:16px;background:var(--grad);color:var(--white);font-family:"Libre Baskerville",serif;font-size:18px;text-transform:uppercase;border-radius:4px;white-space:nowrap}
.btn svg{width:36px;height:12px}

.topbar{top:0;left:0;width:1200px;height:42px;background:var(--grad)}
.topbar .phone{position:absolute;left:960px;top:7px;display:flex;align-items:center;gap:8px;color:var(--white);font-family:"Libre Baskerville",serif;font-size:16px}
.topbar .phone i{width:30px;height:30px;border-radius:50%;background:#3a3222;display:flex;align-items:center;justify-content:center}
.header{top:42px;left:0;width:1200px;height:83px;background:var(--white);box-shadow:0 2px 4px rgba(0,0,0,.05);z-index:2}
.brand{position:absolute;left:88px;top:-26px;width:188px;height:136px;border-radius:50%;background:var(--white);display:flex;align-items:center;justify-content:center}
.brand span{font-family:"Libre Baskerville",serif;font-size:19px;color:var(--gold);letter-spacing:1px}
.nav{position:absolute;top:32px;left:597px;font-size:15px;color:var(--ink)}
.nav a{color:inherit;text-decoration:none;position:absolute;white-space:nowrap}
.nav a.active{color:var(--gold)}
.nav a.active::after{content:"";position:absolute;left:-4px;right:-4px;top:49px;height:3px;background:var(--gold)}

.hero{top:125px;left:0;width:1200px;height:552px;background:linear-gradient(90deg,#c59a4a 0%,#8a6a3a 30%,#2d3550 45%,#b7ad8e 65%,#d9d4bf 100%)}
.hero h1{position:absolute;right:77px;top:160px;text-align:right;font-family:"Anton",sans-serif;font-weight:400;line-height:1}
.hero h1 .l1{display:block;font-size:52px;color:var(--ink)}
.hero h1 .l2{display:block;font-size:70px;color:var(--gold);margin-top:12px}
.hero p{position:absolute;right:77px;top:308px;text-align:right;font-size:16px;line-height:27px;color:#333}
.dots{position:absolute;left:1156px;top:212px}
.dots i{position:absolute;left:0;width:15px;height:15px;border-radius:50%;background:var(--white)}
.dots i.on{background:transparent;border:3px solid var(--gold)}

.kicker{left:0;width:1200px;text-align:center;top:750px;font-family:"Libre Baskerville",serif;font-size:16px;color:var(--gold)}
.section-title{left:0;width:1200px;text-align:center;font-family:"Libre Baskerville",serif;font-weight:400;text-transform:uppercase;color:var(--ink);font-size:40px}

.product h3{position:absolute;font-family:"Libre Baskerville",serif;font-weight:400;font-size:32px;color:var(--ink);text-transform:uppercase;white-space:nowrap}
.product .net{position:absolute;font-size:17px;color:var(--gold)}
.product p{position:absolute;font-size:15px;line-height:27px;width:305px;color:var(--text)}
.photo{position:absolute;border-radius:20px}

.about{top:2418px;left:0;width:1200px;height:520px;background:linear-gradient(90deg,#5a4a33,#8b7b62 40%,#3e5a2c 70%,#2d4b22)}
.about-panel{position:absolute;left:691px;top:2418px;width:416px;height:606px;background:var(--grad);border-radius:0 0 208px 208px;text-align:center;color:var(--white)}
.about-panel h2{font-family:"Libre Baskerville",serif;font-weight:400;font-size:29px;color:var(--ink);margin-top:82px;white-space:nowrap}
.about-panel .sub{font-size:17px;margin-top:10px}
.about-panel p{font-size:15px;line-height:29px;margin:22px 36px 0}
.outline-btn{position:absolute;left:99px;top:379px;width:208px;height:51px;border:2px solid var(--white);border-radius:4px;display:flex;align-items:center;justify-content:center;gap:14px;font-family:"Libre Baskerville",serif;font-size:18px;text-transform:uppercase}

.watch-sub{left:0;width:1200px;text-align:center;top:3112px;font-size:18px;color:var(--gold)}
.video{left:306px;top:3171px;width:588px;height:381px;background:linear-gradient(135deg,#3a3430,#6b5c4d 50%,#8d7e6e)}
.play{position:absolute;left:260px;top:156px;width:68px;height:68px;border-radius:50%;background:rgba(0,0,0,.55);display:flex;align-items:center;justify-content:center}

.subscribe{top:3616px;left:0;width:1200px;height:125px;background:var(--grad)}
.subscribe h2{position:absolute;left:134px;top:46px;width:316px;font-family:"Libre Baskerville",serif;font-weight:400;font-size:26px;color:var(--white);white-space:nowrap}
.subscribe .field{position:absolute;left:464px;top:37px;width:392px;height:51px;background:var(--white);border-radius:4px 0 0 4px;font-size:15px;color:#444;padding:15px 18px}
.subscribe .go{position:absolute;left:856px;top:37px;width:197px;height:51px;background:#d9ab3e;border-radius:0 4px 4px 0;color:var(--white);display:flex;align-items:center;justify-content:center;gap:14px;font-family:"Libre Baskerville",serif;font-size:18px}

.footer h4{position:absolute;font-family:"Libre Baskerville",serif;font-weight:400;font-size:19px;color:var(--ink);text-transform:uppercase}
.contact-item{position:absolute;left:77px;display:flex;gap:18px;font-size:15px;line-height:23px;color:#444}
.contact-item svg{flex:none}
.sitemap{position:absolute;right:77px;top:3812px;text-align:right;font-size:15px;color:#555}
.sitemap li{list-style:none;height:32px}
.sitemap li::after{content:"";display:inline-block;width:6px;height:6px;border-radius:50%;background:var(--gold);margin-left:15px;vertical-align:middle}
.foot-brand{left:506px;top:3784px;width:186px;height:108px;border-radius:50%;background:#2a2419;border:5px solid var(--gold-light);display:flex;align-items:center;justify-content:center;font-family:"Libre Baskerville",serif;font-size:18px;color:var(--gold-light)}
.social i{position:absolute;top:3909px;width:45px;height:45px;border-radius:50%;border:3px solid var(--gold-light)}
.rule{left:77px;top:4003px;width:1046px;height:1px;background:#eee}
.legal{left:0;width:1200px;text-align:center;font-size:15px;color:#444}
</style>
</head>
<body>

<div class="abs topbar">
  <div class="phone"><i><svg width="16" height="16" viewBox="0 0 24 24"><path fill="#fff" d="M6.6 10.8a15 15 0 0 0 6.6 6.6l2.2-2.2c.3-.3.7-.4 1-.2 1.1.4 2.3.6 3.6.6.6 0 1 .4 1 1V20c0 .6-.4 1-1 1A17 17 0 0 1 3 4c0-.6.4-1 1-1h3.5c.6 0 1 .4 1 1 0 1.3.2 2.5.6 3.6.1.3 0 .7-.2 1z"/></svg></i>+642 1000 4417</div>
</div>

<header class="abs header">
  <div class="brand"><span>TOLVENMARSK</span></div>
  <nav class="nav">
    <a class="active" style="left:0">Home</a>
    <a style="left:73px">MGO Manuka Honey</a>
    <a style="left:254px">About Us</a>
    <a style="left:353px">Contact Us</a>
    <svg class="abs" style="left:464px;top:1px" width="18" height="18" viewBox="0 0 24 24"><circle cx="10" cy="10" r="6.5" fill="none" stroke="#222" stroke-width="2.4"/><path d="M15 15l6 6" stroke="#222" stroke-width="2.6"/></svg>
    <svg class="abs" style="left:503px;top:0" width="22" height="20" viewBox="0 0 24 22"><path d="M2 8h20l-2.5 12h-15z" fill="none" stroke="#222" stroke-width="2"/><path d="M7 8l4-6M17 8l-4-6M8 11v6M12 11v6M16 11v6" stroke="#222" stroke-width="1.6"/></svg>
  </nav>
</header>

<section class="abs hero" role="img" aria-label="Close-up photograph of a bee on golden honeycomb">
  <h1><span class="l1">THE PUREST TEAT OF</span><span class="l2">NEW ZELAND</span></h1>
  <p>Lorem Ipsum is simply dummy text of the printing<br>and typesetting industry has been the !</p>
  <div class="btn" style="left:925px;top:377px;width:198px;height:50px">Shop Now <svg viewBox="0 0 36 12"><path d="M0 6h33M28 1l6 5-6 5" fill="none" stroke="#fff" stroke-width="1.6"/></svg></div>
  <div class="dots"><i style="top:0"></i><i style="top:24px"></i><i class="on" style="top:56px"></i><i style="top:86px"></i><i style="top:110px"></i></div>
</section>

<div class="abs kicker">TOLVENMARSK</div>
<h2 class="abs section-title" style="top:778px">Featured Products</h2>

<article class="product">
  <svg class="abs" style="left:630px;top:889px" width="404" height="404"><circle cx="202" cy="202" r="195" fill="none" stroke="var(--gold)" stroke-width="7"/></svg>
  <div class="photo" role="img" aria-label="Jar of manuka honey beside honeycomb and flowers" style="left:736px;top:877px;width:328px;height:366px;background:linear-gradient(160deg,#2b2b2b,#1d5a45 55%,#d9a13a)"></div>
  <h3 style="left:155px;top:993px">Manuka Honey</h3>
  <div class="net" style="left:160px;top:1036px">Net.250g</div>
  <p style="left:160px;top:1072px">Lorem Ipsum is simply dummy text of the printing and typesetting industry has been the !</p>
  <div class="btn" style="left:157px;top:1173px;width:198px;height:50px">Shop Now <svg viewBox="0 0 36 12"><path d="M0 6h33M28 1l6 5-6 5" fill="none" stroke="#fff" stroke-width="1.6"/></svg></div>
</article>

<article class="product">
  <svg class="abs" style="left:157px;top:1384px" width="422" height="422"><circle cx="211" cy="211" r="211" fill="var(--gold-pale)"/><circle cx="211" cy="211" r="185" fill="none" stroke="var(--gold)" stroke-width="7"/></svg>
  <div class="photo" role="img" aria-label="Jar of manuka honey with honeycomb and dripping honey" style="left:280px;top:1456px;width:272px;height:320px;background:linear-gradient(160deg,#2b2b2b,#1d5a45 55%,#e2a73a)"></div>
  <h3 style="left:698px;top:1471px">Multi Floral Honey</h3>
  <div class="net" style="left:704px;top:1514px">Net.250g</div>
  <p style="left:703px;top:1551px">Lorem Ipsum is simply dummy text of the printing and typesetting industry has been the !</p>
  <div class="btn" style="left:699px;top:1650px;width:199px;height:51px">Shop Now <svg viewBox="0 0 36 12"><path d="M0 6h33M28 1l6 5-6 5" fill="none" stroke="#fff" stroke-width="1.6"/></svg></div>
</article>

<article class="product">
  <svg class="abs" style="left:684px;top:1843px" width="404" height="404"><circle cx="202" cy="202" r="195" fill="none" stroke="var(--gold)" stroke-width="7"/></svg>
  <div class="photo" role="img" aria-label="Jar of manuka honey with honey dripping from a dipper" style="left:728px;top:1880px;width:347px;height:336px;background:linear-gradient(160deg,#e8a83a,#2b2b2b 45%,#1d5a45)"></div>
  <h3 style="left:155px;top:1931px">Manuka Honey</h3>
  <div class="net" style="left:160px;top:1974px">Net.250g</div>
  <p style="left:160px;top:2010px">Lorem Ipsum is simply dummy text of the printing and typesetting industry has been the !</p>
  <div class="btn" style="left:157px;top:2109px;width:198px;height:51px">Shop Now <svg viewBox="0 0 36 12"><path d="M0 6h33M28 1l6 5-6 5" fill="none" stroke="#fff" stroke-width="1.6"/></svg></div>
</article>

<div class="btn" style="left:472px;top:2293px;width:256px;height:51px">Explore More <svg viewBox="0 0 36 12"><path d="M0 6h33M28 1l6 5-6 5" fill="none" stroke="#fff" stroke-width="1.6"/></svg></div>

<section class="abs about" role="img" aria-label="Beekeeper lifting a frame from a wooden hive in long grass"></section>
<div class="about-panel">
  <h2>ABOUT TOLVENMARSK</h2>
  <div class="sub">The Purest Test of NewZeland !</div>
  <p>Lorem Ipsum is simply dummy text of the printing and typesetting industry. Lorem Ipsum has been the industry's standard dummy text ever since the 1500s, when an unknown printer took a galley of type and scrambled it to make a type specimen book.</p>
  <div class="outline-btn">Learn More <svg width="36" height="12" viewBox="0 0 36 12"><path d="M0 6h33M28 1l6 5-6 5" fill="none" stroke="#fff" stroke-width="1.6"/></svg></div>
</div>

<h2 class="abs section-title" style="top:3054px">Watch Now !</h2>
<div class="abs watch-sub">The Purest Test of NewZeland !</div>
<div class="abs video" role="img" aria-label="Video still of honey poured over a crepe on a café table">
  <div class="play"><svg width="26" height="28" viewBox="0 0 26 28"><path d="M4 2l20 12-20 12z" fill="#fff"/></svg></div>
</div>

<section class="abs subscribe">
  <h2>STAY UP TO DATE !</h2>
  <div class="field">Enter Email *</div>
  <div class="go">SUBSCRIBE <svg width="36" height="12" viewBox="0 0 36 12"><path d="M0 6h33M28 1l6 5-6 5" fill="none" stroke="#fff" stroke-width="1.6"/></svg></div>
</section>

<footer class="footer">
  <h4 style="left:77px;top:3770px">Contact Us</h4>
  <div class="contact-item" style="top:3826px"><svg width="20" height="28" viewBox="0 0 20 28"><path d="M10 1a9 9 0 0 0-9 9c0 7 9 17 9 17s9-10 9-17a9 9 0 0 0-9-9z" fill="var(--gold)"/><circle cx="10" cy="10" r="3.5" fill="#fff"/></svg><span>101- Lorem ipsum simple<br>text print update.</span></div>
  <div class="contact-item" style="top:3887px"><svg width="20" height="20" viewBox="0 0 24 24"><path fill="var(--gold)" d="M6.6 10.8a15 15 0 0 0 6.6 6.6l2.2-2.2c.3-.3.7-.4 1-.2 1.1.4 2.3.6 3.6.6.6 0 1 .4 1 1V20c0 .6-.4 1-1 1A17 17 0 0 1 3 4c0-.6.4-1 1-1h3.5c.6 0 1 .4 1 1 0 1.3.2 2.5.6 3.6.1.3 0 .7-.2 1z"/></svg><span>+642 1000 4417.</span></div>
  <div class="contact-item" style="top:3925px"><svg width="22" height="16" viewBox="0 0 22 16"><rect width="22" height="16" rx="2" fill="var(--gold)"/><path d="M1 1l10 8 10-8" fill="none" stroke="#fff" stroke-width="1.6"/></svg><span>sales@tolvenmarsk.co.nz</span></div>

  <div class="abs foot-brand">TOLVENMARSK</div>
  <div class="social" aria-label="Social links">
    <i style="left:521px;background:#2b3a5c"></i>
    <i style="left:577px;background:#1f5a8a"></i>
    <i style="left:633px;background:#b82a2a"></i>
  </div>

  <h4 style="right:77px;top:3770px">Sitemap</h4>
  <ul class="sitemap">
    <li>Home</li>
    <li>MGO Manuka Honey</li>
    <li>About Us</li>
    <li>Contact Us</li>
  </ul>

  <div class="abs rule"></div>
  <div class="abs legal" style="top:4032px">©TOLVENMARSK – 2020 &nbsp;All rights reserved.</div>
  <div class="abs legal" style="top:4060px">Terms &amp; Conditions | Privacy Policy</div>
</footer>

</body>
</html>
```